Construction Company

Design a clutter free business card, it can be double-sided utilizing the logo for VKM Ltd simple with all relevant contact information.

Please also a letterhead design to function for the purposes of invoicing, all mail requirements, with header to be distinctive while the footer ties page together and incorporates all necessary information.

For now, please use generic / dummy text and when a winner is selected, I will disclose the contact information.

Hi Designers! Please read the updated brief which includes the design of a business card and letterhead. Thank you!

```html
<!DOCTYPE html>
<html lang="en">
<head>
<meta charset="utf-8">
<title>VKM Ltd Business Card</title>
<link rel="stylesheet" href="https://fonts.googleapis.com/css2?family=Libre+Baskerville:wght@400;700&family=Arimo:wght@400&display=swap">
<style>
  :root {
    --stage: #2a2a2a;
    --navy: #0a2f8c;
    --gold: #b38b00;
    --slate: #5a6a6a;
    --paper: #ffffff;
    --ink: #1c1c1c;
    --rule: #d6d6d6;
  }
  * { margin: 0; padding: 0; box-sizing: border-box; }
  html, body { width: 1200px; height: 900px; overflow: hidden; }
  body {
    background: var(--stage);
    position: relative;
    font-family: "Arimo", Arial, sans-serif;
  }
  .card {
    position: absolute;
    left: 280px;
    width: 640px;
    height: 366px;
    box-shadow: 0 10px 30px rgba(0,0,0,0.5);
  }
  .card--front {
    top: 60px;
    background: linear-gradient(to bottom, var(--gold) 0%, var(--slate) 45%, var(--navy) 100%);
    display: flex;
    align-items: center;
    justify-content: center;
  }
  .card--back {
    top: 474px;
    background: var(--paper);
    display: flex;
    align-items: center;
  }
  .brand-name {
    font-family: "Libre Baskerville", Georgia, serif;
    font-weight: 700;
    font-size: 58px;
    letter-spacing: 1px;
    line-height: 1;
  }
  .card--front .brand-name { color: var(--paper); }
  .card--back .brand-name { color: var(--navy); font-size: 50px; }
  .brand-area {
    width: 330px;
    display: flex;
    justify-content: center;
  }
  .divider {
    width: 1px;
    height: 220px;
    background: var(--rule);
  }
  .contact {
    padding-left: 28px;
    color: var(--ink);
  }
  .contact__name {
    font-family: "Libre Baskerville", Georgia, serif;
    font-weight: 700;
    font-size: 17px;
    color: var(--navy);
    text-transform: uppercase;
  }
  .contact__role {
    font-size: 15px;
    margin-bottom: 14px;
  }
  .contact__list { list-style: none; }
  .contact__item {
    display: flex;
    align-items: center;
    gap: 9px;
    font-size: 15px;
    line-height: 22px;
  }
  .contact__item svg { width: 13px; height: 13px; fill: var(--navy); flex: none; }
  .contact__accent { color: var(--navy); }
  .contact__address {
    margin-top: 14px;
    padding-left: 22px;
    font-size: 15px;
    line-height: 20px;
  }
</style>
</head>
<body>
  <section class="card card--front">
    <span class="brand-name">VKM Ltd</span>
  </section>

  <section class="card card--back">
    <div class="brand-area">
      <span class="brand-name">VKM Ltd</span>
    </div>
    <div class="divider"></div>
    <div class="contact">
      <p class="contact__name">Daniel Hart</p>
      <p class="contact__role">Managing Director</p>
      <ul class="contact__list">
        <li class="contact__item">
          <svg viewBox="0 0 16 16"><path d="M3 1l3 3-2 2c1 2 3 4 6 6l2-2 3 3-2 2C7 15 1 9 1 3z"/></svg>
          020-555 0148
        </li>
        <li class="contact__item">
          <svg viewBox="0 0 16 16"><path d="M4 1h8v14H4zM5.5 2.5v9h5v-9zM8 12.5a1 1 0 100 2 1 1 0 000-2z" fill-rule="evenodd"/></svg>
          077-555 0193
        </li>
        <li class="contact__item">
          <svg viewBox="0 0 16 16"><path d="M1 3h14v10H1zM2 4l6 5 6-5z" fill-rule="evenodd"/></svg>
          info@vkmbuild.com
        </li>
        <li class="contact__item">
          <svg viewBox="0 0 16 16"><circle cx="8" cy="8" r="7"/><path d="M1 8h14M8 1v14M3 4h10M3 12h10" stroke="#fff" stroke-width="1"/></svg>
          <span>www.<span class="contact__accent">vkmbuild</span>.com</span>
        </li>
      </ul>
      <p class="contact__address">18, Harbour Works Road<br>BS1 4QT, United Kingdom</p>
    </div>
  </section>
</body>
</html>
```